7K packaging design

We are a wholesaler for Automotive Spare Parts in Jordan and Iraq market and we needs to import spare parts from China under our company private brand "7K"
The 7K brand’s product lines include Filtration, Braking Systems, Wheels, Wheel Bolts & Nuts, Shock Absorbers, Sensors, Cooling Systems, Axles and more.
The aim of the project is to unify the brand packaging across all the product lines , we will start by the brake pads then based on the approved design we will do the other products

Target Market(s)

Jordan , Iraq Market

Industry/Entity Type

Automotive spare parts

Requirements
Must have
• Name of the product :Ceramic brake pads specs : Superior stopping power Noise suppression Low Dust Technology Made in china
Nice to have
• Brake pad outline image on the box
Should not have
• Blue color

```html
<!DOCTYPE html>
<html lang="en">
<head>
<meta charset="utf-8">
<title>7K packaging design – Ceramic Brake Pads dieline</title>
<link rel="stylesheet" href="https://fonts.googleapis.com/css2?family=Audiowide&family=Montserrat:wght@500;600&display=swap">
<style>
  :root {
    --backdrop: #dcdcdc;
    --red-bright: #ff1010;
    --red-mid: #e00008;
    --red-deep: #7e0005;
    --flap-dark: #333333;
    --photo-light: #a8a8a8;
    --photo-dark: #262626;
    --band-grey: #9b9b9b;
    --silver: #e6e6e6;
    --cut-line: #e0117f;
    --ink-white: #ffffff;
  }
  html, body {
    margin: 0;
    width: 1200px;
    height: 569px;
    overflow: hidden;
    background: var(--backdrop);
  }
  .dieline { display: block; width: 1200px; height: 569px; }
  .flap-dark { fill: var(--flap-dark); }
  .cut { fill: none; stroke: var(--cut-line); stroke-width: 1.2; }
  .silver-stripe { fill: var(--silver); }
  .info-band { fill: var(--band-grey); }
  .product-title {
    font-family: "Audiowide", sans-serif;
    font-style: italic;
    fill: var(--ink-white);
  }
  .brand-name {
    font-family: "Audiowide", sans-serif;
    fill: var(--ink-white);
  }
  .brand-dot { fill: none; stroke: var(--ink-white); stroke-width: 2; }
  .feature-text {
    font-family: "Montserrat", sans-serif;
    font-weight: 600;
    font-size: 5.5px;
    fill: var(--ink-white);
  }
  .origin-text {
    font-family: "Montserrat", sans-serif;
    font-weight: 600;
    font-size: 6.5px;
    letter-spacing: 0.4px;
    fill: var(--ink-white);
  }
  .feature-icon { fill: none; stroke: var(--ink-white); stroke-width: 1.4; }
</style>
</head>
<body>
<svg class="dieline" viewBox="892 100 2130 1010" xmlns="http://www.w3.org/2000/svg">
  <defs>
    <linearGradient id="red-panel" x1="0" y1="0" x2="0" y2="1">
      <stop offset="0" stop-color="var(--red-bright)"/>
      <stop offset="0.55" stop-color="var(--red-mid)"/>
      <stop offset="1" stop-color="var(--red-deep)"/>
    </linearGradient>
    <linearGradient id="red-glow" x1="0" y1="0" x2="1" y2="1">
      <stop offset="0" stop-color="#ff2a2a"/>
      <stop offset="1" stop-color="#b80006"/>
    </linearGradient>
    <radialGradient id="pad-glow" cx="0.5" cy="0.5" r="0.5">
      <stop offset="0" stop-color="#ffffff" stop-opacity="0.28"/>
      <stop offset="0.6" stop-color="#ff6a6a" stop-opacity="0.14"/>
      <stop offset="1" stop-color="#ff1010" stop-opacity="0"/>
    </radialGradient>
    <linearGradient id="photo-tone" x1="0" y1="0" x2="1" y2="1">
      <stop offset="0" stop-color="var(--photo-light)"/>
      <stop offset="1" stop-color="var(--photo-dark)"/>
    </linearGradient>

    <g id="feature-row">
      <circle class="feature-icon" cx="0" cy="0" r="7"/>
      <circle class="feature-icon" cx="0" cy="0" r="2.5"/>
      <text class="feature-text" x="12" y="-4">SUPERIOR</text>
      <text class="feature-text" x="12" y="2">STOPPING</text>
      <text class="feature-text" x="12" y="8">POWER</text>
      <path class="feature-icon" d="M66 -4 h4 l5 -4 v16 l-5 -4 h-4 z M79 -4 l5 -2 M79 0 h6 M79 4 l5 2"/>
      <text class="feature-text" x="90" y="-1">NOISE</text>
      <text class="feature-text" x="90" y="5">SUPPRESSION</text>
      <circle class="feature-icon" cx="157" cy="0" r="7"/>
      <circle class="feature-icon" cx="157" cy="0" r="3"/>
      <text class="feature-text" x="169" y="-1">LOW DUST</text>
      <text class="feature-text" x="169" y="5">TECHNOLOGY</text>
    </g>

    <g id="end-panel">
      <rect x="0" y="0" width="451" height="181" fill="url(#red-glow)"/>
      <ellipse cx="345" cy="75" rx="110" ry="70" fill="url(#pad-glow)" role="img" aria-label="Brake pad outline drawing"/>
      <g role="img" aria-label="Greyscale photo of a truck">
        <polygon points="0,0 239,0 149,181 0,181" fill="url(#photo-tone)"/>
      </g>
      <polygon class="silver-stripe" points="239,0 252,0 162,181 149,181"/>
      <polygon class="info-band" points="186,147 451,147 451,181 169,181"/>
      <use href="#feature-row" transform="translate(210,164)"/>
      <circle class="brand-dot" cx="40" cy="40" r="24"/>
      <text class="brand-name" x="72" y="52" font-size="34">7K</text>
      <text class="product-title" x="14" y="122" font-size="19">Ceramic</text>
      <text class="product-title" x="14" y="140" font-size="19">Brake</text>
      <text class="product-title" x="14" y="158" font-size="19">Pads</text>
    </g>

    <g id="face-panel">
      <rect x="0" y="0" width="451" height="182" fill="url(#red-panel)"/>
      <ellipse cx="315" cy="88" rx="135" ry="80" fill="url(#pad-glow)" role="img" aria-label="Brake pad outline drawing"/>
      <text class="product-title" x="26" y="46" font-size="24">Ceramic</text>
      <text class="product-title" x="26" y="72" font-size="24">Brake</text>
      <text class="product-title" x="26" y="98" font-size="24">Pads</text>
      <use href="#feature-row" transform="translate(32,164)"/>
      <text class="origin-text" x="432" y="168" text-anchor="end">MADE IN CHINA</text>
    </g>

    <g id="side-panel">
      <g role="img" aria-label="Greyscale photo of a truck">
        <rect x="0" y="0" width="213" height="182" fill="url(#photo-tone)"/>
      </g>
      <circle class="brand-dot" cx="80" cy="55" r="26"/>
      <text class="brand-name" x="112" y="68" font-size="36">7K</text>
      <text class="product-title" x="190" y="146" font-size="18" text-anchor="end">Ceramic Brake</text>
      <text class="product-title" x="190" y="164" font-size="18" text-anchor="end">Pads</text>
    </g>
  </defs>

  <rect class="flap-dark" x="1518" y="122" width="213" height="181"/>
  <rect class="flap-dark" x="2182" y="122" width="214" height="181"/>
  <use href="#end-panel" transform="translate(1731,122)"/>

  <rect class="flap-dark" x="1518" y="335" width="213" height="182"/>
  <rect class="flap-dark" x="2182" y="335" width="214" height="182"/>
  <use href="#face-panel" transform="translate(1731,335) rotate(180 225.5 91)"/>

  <use href="#side-panel" transform="translate(1518,517)"/>
  <use href="#end-panel" transform="translate(1731,518) rotate(180 225.5 90.5)"/>
  <use href="#side-panel" transform="translate(2182,517)"/>

  <rect x="1518" y="699" width="213" height="174" fill="url(#red-panel)"/>
  <rect x="2182" y="699" width="214" height="174" fill="url(#red-panel)"/>
  <g class="front-panel">
    <rect x="1731" y="699" width="451" height="213" fill="url(#red-panel)"/>
    <ellipse cx="2040" cy="805" rx="140" ry="90" fill="url(#pad-glow)" role="img" aria-label="Brake pad outline drawing"/>
    <text class="product-title" x="1757" y="752" font-size="26">Ceramic</text>
    <text class="product-title" x="1757" y="779" font-size="26">Brake</text>
    <text class="product-title" x="1757" y="806" font-size="26">Pads</text>
    <use href="#feature-row" transform="translate(1762,874)"/>
    <text class="origin-text" x="2163" y="878" text-anchor="end">MADE IN CHINA</text>
  </g>

  <path d="M1600 912 H2312 C2340 912 2348 940 2340 980 C2325 1050 2290 1095 2240 1095 H1680 C1620 1095 1585 1050 1572 980 C1565 940 1572 912 1600 912 Z" fill="url(#red-panel)"/>

  <g class="cut">
    <rect x="1518" y="122" width="878" height="181"/>
    <rect x="1518" y="335" width="878" height="538"/>
    <line x1="1731" y1="122" x2="1731" y2="1095"/>
    <line x1="2182" y1="122" x2="2182" y2="1095"/>
    <line x1="1731" y1="517" x2="2182" y2="517"/>
    <line x1="1518" y1="699" x2="2396" y2="699"/>
    <line x1="1731" y1="912" x2="2182" y2="912"/>
    <path d="M1582 873 v7 h84 v-7 M2247 873 v7 h84 v-7"/>
  </g>
</svg>
</body>
</html>
```